Looking for a modern, Professional business card design

We have a simple business card, but are looking for a more modern, professional look. A sample of the basic card is attached as well as the logo. We would also like to add that we offer:
Struggling with your finances?
- Learn to become debt free
- Discover the power of cash
- Control your money instead of it controlling you
Let us help you achieve a new level of financial freedom!
Also, we would like to have a "SPECIAL OFFER!: FREE 30 minute consultation"
Financial Planning

```html
<!DOCTYPE html>
<html lang="en">
<head>
<meta charset="utf-8">
<title>Harborline Financial Coaching – Business Card</title>
<link href="https://fonts.googleapis.com/css2?family=Source+Sans+3:ital,wght@0,400;0,600;0,700;1,400&display=swap" rel="stylesheet">
<style>
  :root {
    --backdrop: #3b3b3b;
    --card-white: #ffffff;
    --ink: #1f1f1f;
    --ink-soft: #4a4a4a;
    --brand-green: #4b9a35;
    --brand-green-deep: #3a8a3e;
    --brand-lime: #a6cf3a;
    --rule: #8a8a8a;
    --text-light: #ffffff;
  }
  * { margin: 0; padding: 0; box-sizing: border-box; }
  html, body {
    width: 1105px; height: 1200px; overflow: hidden;
    background: var(--backdrop);
    font-family: "Source Sans 3", "Myriad Pro", sans-serif;
  }
  .card {
    position: absolute; left: 193px; width: 718px;
    overflow: hidden;
  }
  .card-front { top: 181px; height: 413px; background: var(--card-white); }
  .card-back {
    top: 637px; height: 410px;
    background: radial-gradient(ellipse 70% 90% at 36% 50%, var(--brand-lime) 0%, #6db23a 45%, var(--brand-green-deep) 100%);
    color: var(--text-light);
  }
  .accent-circle { position: absolute; border-radius: 50%; }
  .card-front .accent-circle {
    left: 490px; top: -18px; width: 116px; height: 116px;
    background: var(--brand-green); opacity: .1;
  }
  .card-back .accent-circle {
    left: 563px; top: -18px; width: 116px; height: 116px;
    background: var(--text-light); opacity: .14;
  }
  .brand-lockup {
    position: absolute; left: 46px; top: 82px;
    display: flex; align-items: center; gap: 14px;
  }
  .brand-dot { width: 40px; height: 40px; border-radius: 50%; background: var(--brand-green); }
  .brand-name { font-size: 31px; font-weight: 700; color: var(--ink); letter-spacing: .5px; }
  .divider {
    position: absolute; left: 37px; top: 276px; width: 646px;
    border-top: 1.5px solid var(--rule);
  }
  .person { position: absolute; left: 37px; top: 290px; }
  .person-name { font-size: 26px; font-weight: 600; color: var(--brand-green); line-height: 1.2; }
  .person-title { font-size: 20px; color: var(--ink); line-height: 1.3; }
  .contact-list { position: absolute; left: 373px; top: 290px; list-style: none; }
  .contact-list li {
    display: flex; align-items: center; gap: 12px;
    font-size: 19px; color: var(--ink-soft); height: 27.5px;
  }
  .contact-list svg { width: 18px; height: 18px; fill: var(--brand-green); flex: none; }

  .pitch { position: absolute; left: 30px; top: 36px; }
  .pitch-heading { font-size: 19px; font-weight: 700; line-height: 1.3; text-transform: uppercase; }
  .pitch-list { list-style: none; margin-top: 2px; }
  .pitch-list li { font-size: 19px; font-style: italic; line-height: 26.5px; padding-left: 20px; position: relative; }
  .pitch-list li::before {
    content: ""; position: absolute; left: 3px; top: 10px;
    width: 8px; height: 8px; border-radius: 50%; background: var(--text-light);
  }
  .pitch-closer { font-size: 19px; font-style: italic; line-height: 28px; }
  .offer { position: absolute; left: 32px; top: 192px; }
  .offer-title { font-size: 25px; font-weight: 700; line-height: 1.2; }
  .offer-detail { font-size: 17px; font-weight: 700; line-height: 1.3; }
  .brand-wordmark {
    position: absolute; left: 32px; top: 278px;
    font-size: 40px; font-weight: 700; line-height: 1.1; color: var(--text-light);
  }
</style>
</head>
<body>
  <section class="card card-front">
    <div class="accent-circle"></div>
    <div class="brand-lockup">
      <div class="brand-dot"></div>
      <div class="brand-name">Harborline Financial Coaching</div>
    </div>
    <div class="divider"></div>
    <div class="person">
      <p class="person-name">Daniel R. Hayes</p>
      <p class="person-title">Personal Financial Coach</p>
    </div>
    <ul class="contact-list">
      <li><svg viewBox="0 0 24 24" aria-hidden="true"><path d="M7 1h10a2 2 0 0 1 2 2v18a2 2 0 0 1-2 2H7a2 2 0 0 1-2-2V3a2 2 0 0 1 2-2zm0 3v14h10V4H7zm5 15.5a1.2 1.2 0 1 0 0 2.4 1.2 1.2 0 0 0 0-2.4z"/></svg>(555) 014-2278</li>
      <li><svg viewBox="0 0 24 24" aria-hidden="true"><path d="M2 5h20v14H2V5zm2 2v.5l8 5.5 8-5.5V7H4zm0 2.9V17h16V9.9l-8 5.5-8-5.5z"/></svg>daniel@harborlinecoaching.com</li>
      <li><svg viewBox="0 0 24 24" aria-hidden="true"><path d="M12 2a10 10 0 1 0 0 20 10 10 0 0 0 0-20zm0 2c.9 1.2 1.6 2.6 2 4h-4c.4-1.4 1.1-2.8 2-4zM4.3 14a8 8 0 0 1 0-4h3.4a16 16 0 0 0 0 4H4.3zm.9 2h3a14 14 0 0 0 1.4 3.6A8 8 0 0 1 5.2 16zm3-8h-3a8 8 0 0 1 4.4-3.6A14 14 0 0 0 8.2 8zM12 20c-.9-1.2-1.6-2.6-2-4h4c-.4 1.4-1.1 2.8-2 4zm2.3-6H9.7a14 14 0 0 1 0-4h4.6a14 14 0 0 1 0 4zm.1 5.6a14 14 0 0 0 1.4-3.6h3a8 8 0 0 1-4.4 3.6zm1.9-5.6a16 16 0 0 0 0-4h3.4a8 8 0 0 1 0 4h-3.4zM15.8 8a14 14 0 0 0-1.4-3.6A8 8 0 0 1 18.8 8h-3z"/></svg>www.harborlinecoaching.com</li>
    </ul>
  </section>

  <section class="card card-back">
    <div class="accent-circle"></div>
    <div class="pitch">
      <h2 class="pitch-heading">Struggling with your finances?</h2>
      <ul class="pitch-list">
        <li>Learn to become debt free</li>
        <li>Discover the power of cash</li>
        <li>Control your money instead of it controlling you</li>
      </ul>
      <p class="pitch-closer">Let us help you achieve a new level of financial freedom!</p>
    </div>
    <div class="offer">
      <p class="offer-title">SPECIAL OFFER!</p>
      <p class="offer-detail">FREE 30 minute consultation</p>
    </div>
    <div class="brand-wordmark">Harborline<br>Financial Coaching</div>
  </section>
</body>
</html>
```